Very visible CoWorking Building Sign overlooking downtown LA and 110 freeway

Our building is drab but very visible and in the best location. We need a great sign for our monolith that overlooks downtown LA and the 100 freeway. We are a new CoWorking business and would like to have a few things we do on the sign: private offices, virtual offices, CoWorking Lounge. Everything we have seen is ho-hum. Can you get us noticed? We need people to know what we do and that we are here but in a creative, professional, unique sign.
Target Market(s)
People who have a business in DTLA, remote workers and those who work from home who need a professional address.
Requirements
Must have
- Our logo (which can be somewhat reimagined) which has our address 2417 on it. The three things we focus on: Private Offices, Virtual Offices, CoWorking Lounge. Incorporate some Navy. Readable from several hundred feet away.
Nice to have
- Mural feel? Something inspirational in this crazy COVID times? Graphics? Color block. I like the idea of decorative but it has to be readable as a building sign. The same with the use of colors. Our colors are grays and navy but with a pop of the chartreuse (we have 2 velvet chartreuse chairs in the space). Helpful to view our website: Harborview2417.com.
Should not have
- Not too graffiti. Keep it professional but unique and wow.

```html
<!DOCTYPE html>
<html lang="en">
<head>
<meta charset="utf-8">
<title>Harborview 2417 Building Sign</title>
<link href="https://fonts.googleapis.com/css2?family=Montserrat:wght@500;600;700&display=swap" rel="stylesheet">
<style>
  :root {
    --navy: #1a3560;
    --royal: #0d4c8c;
    --royal-deep: #0f4683;
    --white: #ffffff;
    --mist: #f5f5f5;
    --forest: #007549;
    --green: #04ad4f;
    --lime: #a6cf39;
    --ring: #8cc63f;
  }
  * { margin: 0; padding: 0; box-sizing: border-box; }
  html, body { width: 933px; height: 1200px; overflow: hidden; background: var(--mist); }
  .sign {
    position: relative;
    width: 933px;
    height: 1200px;
    font-family: "Montserrat", sans-serif;
    overflow: hidden;
    background: var(--mist);
  }
  .sign-top {
    position: absolute;
    left: 0; top: 0;
    width: 933px; height: 520px;
    background: linear-gradient(180deg, #f3f3f3 0%, #ffffff 100%);
  }
  .band { position: absolute; left: 0; width: 933px; }
  .band-lime { top: 520px; height: 14px; background: var(--lime); }
  .band-green { top: 534px; height: 14px; background: var(--green); }
  .band-forest { top: 548px; height: 14px; background: var(--forest); }
  .sign-field {
    position: absolute;
    left: 0; top: 562px;
    width: 933px; height: 576px;
    background: radial-gradient(ellipse at 50% 50%, #0a56a0 0%, var(--royal-deep) 75%);
  }
  .base-forest { top: 1138px; height: 22px; background: var(--forest); }
  .base-green { top: 1160px; height: 20px; background: var(--green); }
  .base-lime { top: 1180px; height: 20px; background: var(--lime); }

  .brand {
    position: absolute;
    left: 0; right: 0;
    top: 118px;
    text-align: center;
    color: var(--navy);
    font-weight: 500;
    line-height: 1;
  }
  .brand-number { font-size: 60px; letter-spacing: 20px; padding-left: 20px; }
  .brand-name { font-size: 100px; letter-spacing: 3px; margin-top: 24px; }

  .service {
    position: absolute;
    left: 130px;
    width: 728px;
    height: 86px;
    background: var(--white);
    border-radius: 43px;
    display: flex;
    align-items: center;
  }
  .service-icon {
    position: absolute;
    left: -55px;
    top: -11px;
    width: 108px;
    height: 108px;
    border-radius: 50%;
    background: var(--white);
    border: 5px solid var(--ring);
    display: flex;
    align-items: center;
    justify-content: center;
  }
  .service-label {
    margin-left: 77px;
    color: var(--navy);
    font-weight: 700;
    font-size: 53px;
    letter-spacing: -1.5px;
    white-space: nowrap;
  }
  .service-private { top: 613px; }
  .service-virtual { top: 740px; }
  .service-lounge { top: 866px; }
  .web {
    position: absolute;
    left: 0; right: 0;
    top: 986px;
    text-align: center;
    color: var(--white);
    font-weight: 600;
    font-size: 42px;
    letter-spacing: 4px;
  }
</style>
</head>
<body>
<main class="sign">
  <div class="sign-top"></div>
  <div class="band band-lime"></div>
  <div class="band band-green"></div>
  <div class="band band-forest"></div>
  <div class="sign-field"></div>
  <div class="band base-forest"></div>
  <div class="band base-green"></div>
  <div class="band base-lime"></div>

  <header class="brand">
    <div class="brand-number">2417</div>
    <div class="brand-name">HARBORVIEW</div>
  </header>

  <section class="services">
    <div class="service service-private">
      <span class="service-icon"><svg width="50" height="40" viewBox="0 0 50 40"><path d="M4 20H42M26 5L43 20L26 35" fill="none" stroke="var(--navy)" stroke-width="7" stroke-linecap="round" stroke-linejoin="round"/></svg></span>
      <span class="service-label">PRIVATE OFFICES</span>
    </div>
    <div class="service service-virtual">
      <span class="service-icon"><svg width="50" height="40" viewBox="0 0 50 40"><path d="M4 20H42M26 5L43 20L26 35" fill="none" stroke="var(--navy)" stroke-width="7" stroke-linecap="round" stroke-linejoin="round"/></svg></span>
      <span class="service-label">VIRTUAL OFFICES</span>
    </div>
    <div class="service service-lounge">
      <span class="service-icon"><svg width="50" height="40" viewBox="0 0 50 40"><path d="M4 20H42M26 5L43 20L26 35" fill="none" stroke="var(--navy)" stroke-width="7" stroke-linecap="round" stroke-linejoin="round"/></svg></span>
      <span class="service-label">COWORKING LOUNGE</span>
    </div>
  </section>

  <p class="web">www.harborview2417.com</p>
</main>
</body>
</html>
```